Website Redesign using existing images, copy etc.

I'm looking for a website redesign/refresh of my current WordPress website. I would like to utilize the same photography, a new photo viewer, and an overall refresh of the entire design. This will need to be WordPress with simple accessibility to make changes as we add additional properties and make updates. We auction luxury real estate and luxury yachts for non-distressed sellers. It needs to be simple, luxurious and with ease of use for both web and especially mobile. www.BrindleHarrow.com

```html
<!DOCTYPE html>
<html lang="en">
<head>
<meta charset="utf-8">
<title>Brindle Harrow – Real Estate &amp; Yachts</title>
<link rel="stylesheet" href="https://fonts.googleapis.com/css2?family=Merriweather:wght@400;700&family=Sarabun:wght@400;500&family=Tinos:wght@400;700&display=swap">
<style>
:root{
  --olive:#8f8866;
  --olive-dark:#7d7656;
  --ink:#111;
  --text:#2b2b2b;
  --white:#fff;
  --paper:#dedcd2;
  --footer:#000;
}
*{box-sizing:border-box;margin:0;padding:0}
html,body{width:1200px;height:2678px;overflow:hidden;background:var(--white)}
body{position:relative;font-family:"Sarabun",sans-serif;color:var(--text)}
.abs{position:absolute}
.pill{position:absolute;border-radius:30px;background:var(--olive);color:var(--white);display:flex;align-items:center;justify-content:center;font-family:"Merriweather",serif;font-weight:700;box-shadow:0 3px 6px rgba(0,0,0,.2);white-space:nowrap}
.brand{display:flex;align-items:center;gap:12px;font-family:"Tinos",serif;letter-spacing:7px;font-size:22px;white-space:nowrap}
.brand-ring{width:44px;height:44px;border:2px solid currentColor;border-radius:50%;flex:none}

/* header */
.site-header{position:absolute;left:0;top:0;width:1200px;height:85px;background:var(--white)}
.site-header .brand{position:absolute;left:97px;top:20px;color:var(--olive)}
.main-nav{position:absolute;left:588px;top:33px;display:flex;gap:44px;font-family:"Tinos",serif;font-size:16px;color:var(--ink)}
.phone-pill{left:946px;top:20px;width:154px;height:46px;font-size:16px;letter-spacing:1px}

/* hero */
.hero{position:absolute;left:0;top:85px;width:1200px;height:601px;overflow:hidden;
  background:linear-gradient(180deg,#6c5a5a 0%,#8a6d58 18%,#4c5a3d 45%,#6b5557 70%,#2f3b26 100%)}
.hero-shade{position:absolute;inset:0;background:linear-gradient(90deg,rgba(0,0,0,.35),rgba(0,0,0,0) 60%)}
.hero-welcome{left:96px;top:180px;font-family:"Merriweather",serif;font-size:31px;color:var(--white)}
.hero-title{left:95px;top:225px;font-family:"Merriweather",serif;font-weight:700;font-size:50px;color:var(--white);white-space:nowrap}
.hero-sub{left:99px;top:297px;font-size:21px;color:var(--white)}
.hero-btn{top:337px;height:46px;font-family:"Tinos",serif;font-size:15px}
.hero-dots{left:100px;top:432px}

/* intro */
.intro-title{left:97px;top:785px;width:520px;font-family:"Merriweather",serif;font-weight:700;font-size:32px;line-height:43px;color:var(--ink)}
.intro-kicker{left:97px;top:880px;font-family:"Merriweather",serif;font-size:18px;color:var(--olive)}
.intro-copy{left:97px;top:918px;width:500px;font-size:16px;line-height:32.5px}
.read-more{left:98px;top:1096px;width:137px;height:47px;font-size:17px}

/* featured */
.featured{position:absolute;left:0;top:1243px;width:1200px;height:426px;
  background:linear-gradient(160deg,#938c6a,#867f5e 50%,#8e8766)}
.featured h2{position:absolute;left:0;width:1200px;top:50px;text-align:center;font-family:"Merriweather",serif;font-weight:700;font-size:32px;color:var(--white)}
.press-card{position:absolute;top:119px;width:179px;height:105px;background:#f6f5f0;display:flex;align-items:center;justify-content:center}
.press-badge{width:138px;height:72px;background:#e2e0d8}
.featured p{position:absolute;left:140px;width:920px;top:250px;text-align:center;font-size:16px;line-height:31px;color:var(--white)}
.view-press{left:532px;top:324px;width:136px;height:47px;background:var(--white);color:var(--olive);font-size:16px}

/* sold */
.sold-title{left:621px;top:1730px;font-family:"Merriweather",serif;font-weight:700;font-size:33px;color:var(--ink);white-space:nowrap}
.sold-copy{left:621px;top:1780px;width:485px;font-size:16px;line-height:31px}
.sold-copy p+p{margin-top:31px}
.view-more{left:621px;top:2137px;width:137px;height:47px;font-size:17px}

/* footer */
.site-footer{position:absolute;left:0;top:2262px;width:1200px;height:416px;background:var(--footer);color:var(--white)}
.site-footer .brand{position:absolute;left:98px;top:56px;color:var(--white);font-size:21px;letter-spacing:6px;gap:10px}
.site-footer .brand-ring{width:40px;height:40px}
.footer-head{font-family:"Tinos",serif;font-size:23px;color:var(--white);white-space:nowrap}
.quick-links{position:absolute;left:517px;top:60px}
.quick-links ul{list-style:none;margin-top:12px}
.quick-links li{display:flex;align-items:center;gap:10px;font-size:16px;height:31px}
.signup{position:absolute;left:745px;top:60px}
.field{position:absolute;left:0;width:355px;height:44px;border:1px solid var(--white);border-radius:24px;padding-left:27px;display:flex;align-items:center;font-family:"Merriweather",serif;font-size:16px}
.submit{left:5px;top:165px;width:137px;height:47px;font-size:16px}
.social{position:absolute;top:2519px;width:36px;height:36px;border-radius:50%;background:var(--olive)}
.footer-rule{position:absolute;left:98px;top:355px;width:1003px;height:1px;background:#bbb}
.legal{position:absolute;top:378px;font-size:16px;white-space:nowrap}
</style>
</head>
<body>

<header class="site-header">
  <div class="brand"><span>BRINDLE</span><span class="brand-ring"></span><span>HARROW</span></div>
  <nav class="main-nav"><span>BUY</span><span>SELL</span><span>ABOUT</span><span>CONTACT</span></nav>
  <div class="pill phone-pill">800-555-0172</div>
</header>

<section class="hero" role="img" aria-label="Dusk photograph of a Mediterranean-style luxury estate with palm trees and a brick driveway">
  <div class="hero-shade"></div>
  <svg class="abs" style="left:0;top:0" width="1200" height="601" aria-hidden="true">
    <polygon points="890,0 1200,0 1045,145" fill="var(--olive)" opacity=".85"/>
    <polygon points="1200,420 1200,601 970,601 1075,470" fill="var(--olive)" opacity=".8"/>
    <polygon points="765,165 917,317 765,469 613,317" fill="var(--olive)"/>
    <circle cx="765" cy="315" r="43" fill="none" stroke="#fff" stroke-width="4"/>
  </svg>
  <div class="abs hero-welcome">WELCOME TO</div>
  <div class="abs hero-title">BRINDLE HARROW</div>
  <div class="abs hero-sub">Real Estate &amp; Yachts</div>
  <div class="pill hero-btn" style="left:99px;width:247px">BROWSE UPCOMING AUCTIONS</div>
  <div class="pill hero-btn" style="left:357px;width:246px">BROWSE PAST SUCCESSES</div>
  <svg class="abs hero-dots" width="95" height="20" aria-hidden="true">
    <path d="M30 10H2M9 3L2 10l7 7" stroke="#ccc" stroke-width="2" fill="none"/>
    <circle cx="47" cy="10" r="4.5" fill="#fff"/>
    <path d="M62 10h29M84 3l7 7-7 7" stroke="#fff" stroke-width="2" fill="none"/>
  </svg>
</section>

<h1 class="abs intro-title">Over One Billion Dollars of Auctions Marketed</h1>
<div class="abs intro-kicker">Real Estate &amp; Yachts</div>
<p class="abs intro-copy">The experience of hearing the auctioneer’s final proclamation of “SOLD!” is unparalleled. Whether it’s the initial meeting with the seller at their estate or yacht, or the triumphant raising of the paddle by the winning buyer, we relish every moment of the process and the ensuing festivities. We’re confident that you will, too.</p>
<div class="pill read-more">Read More</div>
<svg class="abs" style="left:672px;top:755px" width="426" height="426" aria-hidden="true">
  <circle cx="213" cy="213" r="210" fill="none" stroke="var(--olive)" stroke-width="3"/>
  <path d="M213 23 A190 190 0 1 1 23 213" fill="none" stroke="var(--olive)" stroke-width="3"/>
  <line x1="23" y1="213" x2="48" y2="213" stroke="var(--olive)" stroke-width="3"/>
</svg>
<div class="abs" role="img" aria-label="Covered porch with wicker furniture overlooking palms and an ocean sunset" style="left:718px;top:801px;width:334px;height:334px;border-radius:50%;background:linear-gradient(135deg,#c9a37f,#7d8a70 40%,#d8d8d4 70%,#8e8a80)"></div>

<section class="featured" role="img" aria-label="Faded aerial photograph of a waterfront coastline">
  <h2>As Featured In</h2>
  <div class="press-card" style="left:121px"><div class="press-badge"></div></div>
  <div class="press-card" style="left:316px"><div class="press-badge"></div></div>
  <div class="press-card" style="left:511px"><div class="press-badge"></div></div>
  <div class="press-card" style="left:706px"><div class="press-badge"></div></div>
  <div class="press-card" style="left:901px"><div class="press-badge"></div></div>
  <p>By offering top-tier properties and vessels globally, along with strategic auction dates, exceptional marketing tactics, and a diligent public relations team, even the most prominent media outlets have taken notice. Check out some of our latest press features.</p>
  <div class="pill view-press">View Press</div>
</section>

<div class="abs" style="left:193px;top:1780px;width:264px;height:361px;border:3px solid var(--olive)"></div>
<div class="abs" style="left:205px;top:1793px;width:240px;height:334px;background:var(--paper)"></div>
<div class="abs" role="img" aria-label="Grand estate entrance lit at dusk with a stone courtyard" style="left:98px;top:1751px;width:241px;height:330px;background:linear-gradient(180deg,#4d5c80,#b8a58a 45%,#8e7a62 75%,#c9bba6)"></div>
<div class="abs" role="img" aria-label="Luxury motor yacht cruising on blue water" style="left:351px;top:1838px;width:240px;height:331px;background:linear-gradient(180deg,#4f86c6,#9dbfe0 50%,#1f3a66 68%,#6d9bd0)"></div>

<h2 class="abs sold-title">Sold by Brindle Harrow</h2>
<div class="abs sold-copy">
  <p>Brindle Harrow is a top-tier destination for luxury property auctions, having overseen the auction marketing of numerous high-end estates and yachts. Our team of luxurycommitted to helping property owners obtain the best value for their assets while ensuring a timely sale. Whether you have an expansive necessary skills and expertise to facilitate various luxury real estate auctions.</p>
  <p>What’s even better? Our team takes care of every aspect of the process in cooperation with tour realtor/broker, including property tours, photography and cinematography, marketing advertising, public relations and more.</p>
</div>
<div class="pill view-more">View More</div>

<footer class="site-footer">
  <div class="brand"><span>BRINDLE</span><span class="brand-ring"></span><span>HARROW</span></div>
  <div class="abs" style="left:213px;top:112px;width:106px;height:124px;border-radius:50% 50% 8px 8px;background:var(--olive)"></div>
  <div class="quick-links">
    <div class="footer-head">QUICK LINKS</div>
    <ul>
      <li><svg width="14" height="14"><path d="M1 7h10M7 2l5 5-5 5" stroke="#fff" stroke-width="2.5" fill="none"/></svg>Home</li>
      <li><svg width="14" height="14"><path d="M1 7h10M7 2l5 5-5 5" stroke="#fff" stroke-width="2.5" fill="none"/></svg>Buy</li>
      <li><svg width="14" height="14"><path d="M1 7h10M7 2l5 5-5 5" stroke="#fff" stroke-width="2.5" fill="none"/></svg>Sell</li>
      <li><svg width="14" height="14"><path d="M1 7h10M7 2l5 5-5 5" stroke="#fff" stroke-width="2.5" fill="none"/></svg>About</li>
      <li><svg width="14" height="14"><path d="M1 7h10M7 2l5 5-5 5" stroke="#fff" stroke-width="2.5" fill="none"/></svg>Blog</li>
      <li><svg width="14" height="14"><path d="M1 7h10M7 2l5 5-5 5" stroke="#fff" stroke-width="2.5" fill="none"/></svg>Contact</li>
    </ul>
  </div>
  <div class="signup">
    <div class="footer-head">SIGN UP FOR BRINDLE ALERTS</div>
    <div class="field" style="top:42px">Name</div>
    <div class="field" style="top:102px">Email</div>
    <div class="pill submit">Submit</div>
  </div>
  <div class="footer-rule"></div>
  <div class="legal" style="left:100px">Copyrights@2023.Brindle Harrow.All Rights Reserved</div>
  <div class="legal" style="left:823px">Terms of service</div>
  <div class="legal" style="left:962px">policyprivacy policy</div>
</footer>
<div class="social" style="left:183px"></div>
<div class="social" style="left:226px"></div>
<div class="social" style="left:269px"></div>
<div class="social" style="left:312px"></div>

</body>
</html>
```